2018 Desk Calendar Design with Better Spine, Better Health with Chiropractic

In conjunction with the Federation of Spinal Wellness Malaysia (FSW), we are organizing a 2018 desk calendar design. The cover page and monthly design size is 210mm (H) x 195mm (W). The will be a total of 27 designs including a cover page (front) [Sample 1], cover page (back) Malaysia National & States Holiday 2018 (https://restdaylist.example.my/2018-dates/) [Sample 2], 12 months design (front) [Sample 3 and 4], 12 months design (back) [Sample 5], Last page (2017 and 2019 calendar) [Sample 6].

Below are some recommendations for monthly back cover design. The main theme remain as Better SPINE, Better HEALTH with CHIROPRACTIC. Each month can in collaborate with of the following element:-

Suggestion 1 (Celebration of the Month)
January - New Year
February - Chinese New Year
March -
April -
May - Labour Day
June - Aidilfitri Festival
July-
August - Independent Day
September - Malaysia Day
October - World Spine Day
November - Deepavali Festival
December - Christmas

Suggestion 2 (States in Malaysia)
January - Perlis
February - Kedah
March - Penang
April - Perak
May - Selangor
June - Negeri Sembilan
July- Melaka
August - Johor
September - Pahang
October - Terengganu
November - Kelantan
December - Sabah & Sarawak

Target Market(s)

Chiropractors and Public

Industry/Entity Type

Chiropractor

Colors

Designer to choose colors to be used in the design.

Requirements
Must have
• The theme for the desk calendar design is Better Spine, Better Health with Chiropractic.
• The cover page should include 5th Anniversary element.
Nice to have
• Lunar or Islamic calendar is optional in the Gregorian calendar.
• AI Format
• Footnote of each page www.spinefsw.example.org

```html
<!DOCTYPE html>
<html lang="en">
<head>
<meta charset="utf-8">
<title>December 2018 – Federation of Spinal Wellness Malaysia Desk Calendar</title>
<link rel="stylesheet" href="https://fonts.googleapis.com/css2?family=Orbitron:wght@700&family=Michroma&family=Old+Standard+TT&family=Arimo&display=swap">
<style>
  :root {
    --page-bg: #cdbdcf;
    --ink: #161616;
    --sunday: #e3211f;
    --rule: #a2243a;
    --plum: #7a2a78;
    --spine: #4c0f33;
    --band: #8a3f8a;
    --fact: #5a1838;
  }
  html, body {
    margin: 0;
    padding: 0;
    overflow: hidden;
    background: var(--page-bg);
  }
  .calendar-page {
    position: relative;
    width: 1107px;
    height: 1200px;
    overflow: hidden;
    background: var(--page-bg);
  }
  .calendar-page svg { position: absolute; inset: 0; }
  .day-head, .day-num { font-family: "Orbitron", sans-serif; font-weight: 700; font-size: 28px; fill: var(--ink); }
  .day-head { font-size: 27px; }
  .sun { fill: var(--sunday); }
  .week-rule { stroke: var(--rule); stroke-width: 1.6; }
  .month-title { font-family: "Michroma", sans-serif; fill: var(--plum); }
  .mini-title { font-family: "Michroma", sans-serif; font-size: 18px; fill: var(--ink); letter-spacing: 2px; }
  .mini-num { font-family: "Orbitron", sans-serif; font-weight: 700; font-size: 14px; fill: var(--ink); }
  .mini-num.sun { fill: var(--sunday); }
  .brand-name { font-family: "Michroma", sans-serif; font-size: 22px; fill: var(--plum); }
  .spine-fact { font-family: "Old Standard TT", serif; font-size: 30px; fill: var(--fact); }
  .site-url { font-family: "Arimo", sans-serif; font-size: 19px; fill: var(--ink); }
</style>
</head>
<body>
<main class="calendar-page">
<svg width="1107" height="1200" viewBox="0 0 1107 1200" xmlns="http://www.w3.org/2000/svg">
  <defs>
    <linearGradient id="photoTones" x1="0" y1="0" x2="1" y2="1">
      <stop offset="0" stop-color="#c9c4c6"/>
      <stop offset="0.35" stop-color="#b48a77"/>
      <stop offset="0.6" stop-color="#e6ecf1"/>
      <stop offset="1" stop-color="#3f8fbf"/>
    </linearGradient>
  </defs>

  <!-- Photo area -->
  <path role="img" aria-label="Photo of medical staff in scrubs looking at a clipboard"
        d="M0,690 C320,720 640,900 1107,1130 L1107,1200 L0,1200 Z" fill="url(#photoTones)"/>

  <!-- Swoosh band -->
  <path d="M0,610 C330,680 660,860 1107,1120 L1107,1170 C660,900 330,720 0,690 Z" fill="var(--band)" opacity="0.75"/>

  <!-- Spine illustration area -->
  <path role="img" aria-label="Illustration of a row of spine vertebrae sweeping across the page"
        d="M20,548 C150,600 300,700 460,820 C600,920 780,950 900,990 C980,1020 1050,1080 1095,1140"
        fill="none" stroke="var(--spine)" stroke-width="66" stroke-linecap="round"/>

  <!-- Weekday header -->
  <g class="weekdays">
    <text class="day-head" x="211" y="103">M</text>
    <text class="day-head" x="330" y="103">T</text>
    <text class="day-head" x="463" y="103">W</text>
    <text class="day-head" x="594" y="103">T</text>
    <text class="day-head" x="724" y="103">F</text>
    <text class="day-head" x="852" y="103">S</text>
    <text class="day-head sun" x="983" y="103">S</text>
  </g>

  <!-- December grid -->
  <g class="month-grid">
    <text class="day-num" x="206" y="192">31</text>
    <text class="day-num" x="852" y="192">1</text>
    <text class="day-num sun" x="983" y="192">2</text>
    <line class="week-rule" x1="193" y1="202" x2="1081" y2="202"/>

    <text class="day-num" x="211" y="288">3</text>
    <text class="day-num" x="330" y="288">4</text>
    <text class="day-num" x="463" y="288">5</text>
    <text class="day-num" x="594" y="288">6</text>
    <text class="day-num" x="724" y="288">7</text>
    <text class="day-num" x="852" y="288">8</text>
    <text class="day-num sun" x="983" y="288">9</text>
    <line class="week-rule" x1="193" y1="297" x2="1081" y2="297"/>

    <text class="day-num" x="211" y="384">10</text>
    <text class="day-num" x="330" y="384">11</text>
    <text class="day-num" x="463" y="384">12</text>
    <text class="day-num" x="594" y="384">13</text>
    <text class="day-num" x="724" y="378">14</text>
    <text class="day-num" x="852" y="378">15</text>
    <text class="day-num sun" x="983" y="378">16</text>
    <line class="week-rule" x1="193" y1="392" x2="1081" y2="392"/>

    <text class="day-num" x="211" y="481">17</text>
    <text class="day-num" x="330" y="481">18</text>
    <text class="day-num" x="463" y="481">19</text>
    <text class="day-num" x="594" y="481">20</text>
    <text class="day-num" x="724" y="474">21</text>
    <text class="day-num" x="852" y="472">22</text>
    <text class="day-num sun" x="983" y="472">23</text>
    <line class="week-rule" x1="193" y1="491" x2="1081" y2="491"/>

    <text class="day-num" x="211" y="577">24</text>
    <text class="day-num" x="330" y="577">25</text>
    <text class="day-num" x="463" y="577">26</text>
    <text class="day-num" x="594" y="577">27</text>
    <text class="day-num" x="724" y="570">28</text>
    <text class="day-num" x="852" y="568">29</text>
    <text class="day-num sun" x="983" y="568">30</text>
    <line class="week-rule" x1="193" y1="583" x2="1081" y2="583"/>
  </g>

  <!-- Brand mark -->
  <g class="brand">
    <circle cx="424" cy="656" r="8" fill="var(--plum)"/>
    <text class="brand-name" x="440" y="666">FSW</text>
  </g>

  <!-- Month title -->
  <text class="month-title" x="549" y="678" textLength="530" lengthAdjust="spacingAndGlyphs">
    <tspan font-size="72">D</tspan><tspan font-size="56">ECEMBER</tspan>
  </text>

  <!-- Previous month -->
  <g class="mini-month">
    <text class="mini-title" x="874" y="716">NOVEMBER</text>
    <g>
      <text class="mini-num" x="826" y="752">M</text><text class="mini-num" x="859" y="752">T</text><text class="mini-num" x="899" y="752">W</text><text class="mini-num" x="935" y="752">T</text><text class="mini-num" x="973" y="752">F</text><text class="mini-num" x="1010" y="752">S</text><text class="mini-num sun" x="1047" y="752">S</text>
      <text class="mini-num" x="935" y="775">1</text><text class="mini-num" x="973" y="775">2</text><text class="mini-num" x="1010" y="775">3</text><text class="mini-num sun" x="1047" y="775">4</text>
      <text class="mini-num" x="826" y="805">5</text><text class="mini-num" x="859" y="805">6</text><text class="mini-num" x="899" y="805">7</text><text class="mini-num" x="935" y="805">8</text><text class="mini-num" x="973" y="805">9</text><text class="mini-num" x="1010" y="805">10</text><text class="mini-num sun" x="1047" y="805">11</text>
      <text class="mini-num" x="826" y="836">12</text><text class="mini-num" x="859" y="836">13</text><text class="mini-num" x="899" y="836">14</text><text class="mini-num" x="935" y="836">15</text><text class="mini-num" x="973" y="836">16</text><text class="mini-num" x="1010" y="836">17</text><text class="mini-num sun" x="1047" y="836">18</text>
      <text class="mini-num" x="826" y="867">19</text><text class="mini-num" x="859" y="867">20</text><text class="mini-num" x="899" y="867">21</text><text class="mini-num" x="935" y="867">22</text><text class="mini-num" x="973" y="867">23</text><text class="mini-num" x="1010" y="867">24</text><text class="mini-num sun" x="1047" y="867">25</text>
      <text class="mini-num" x="826" y="897">26</text><text class="mini-num" x="859" y="897">27</text><text class="mini-num" x="899" y="897">28</text><text class="mini-num" x="935" y="897">29</text><text class="mini-num" x="973" y="897">30</text><text class="mini-num" x="1010" y="897">31</text>
    </g>
  </g>

  <!-- Spine fact -->
  <g text-anchor="end">
    <text class="spine-fact" x="938" y="1090">Spine Fact:</text>
    <text class="spine-fact" x="938" y="1129">An average spinal</text>
    <text class="spine-fact" x="938" y="1168">cord weighs 35 grams</text>
  </g>

  <!-- Footer web address -->
  <text class="site-url" x="12" y="1194">www.spinefsw.example.org</text>
</svg>
</main>
</body>
</html>
```